Dalvick's Business Card

I need some designs for a new business card including the new logo attached. An old example of our business card is also attached to show all the data that should be included on the new design.
**I added some more examples someone had mocked up**

Contact Information for Business Card

Should include all info on other examples uploaded.

```html
<!DOCTYPE html>
<html lang="en">
<head>
<meta charset="utf-8">
<title>Dalvick's Business Card</title>
<link href="https://fonts.googleapis.com/css2?family=Poppins:wght@400;500;600;700&display=swap" rel="stylesheet">
<style>
  :root {
    --backdrop: #2b2422;
    --card: #1b1b1c;
    --blue: #0a74c9;
    --red: #ee2028;
    --white: #ffffff;
  }
  * { box-sizing: border-box; margin: 0; padding: 0; }
  html, body { width: 1200px; height: 842px; overflow: hidden; }
  body {
    background: var(--backdrop);
    font-family: "Poppins", sans-serif;
    display: flex;
    align-items: center;
    justify-content: center;
    gap: 30px;
  }
  .card {
    position: relative;
    width: 550px;
    height: 314px;
    background: var(--card);
    box-shadow: 0 14px 34px rgba(0,0,0,.55);
    overflow: hidden;
    display: flex;
    flex-direction: column;
    align-items: center;
    justify-content: center;
    text-align: center;
  }

  /* Contact side */
  .contact .band {
    position: absolute; left: 0; right: 0; height: 14px; background: var(--blue);
  }
  .contact .band.top { top: 0; }
  .contact .band.bottom { bottom: 0; }
  .person-name {
    color: var(--blue); font-weight: 600; font-size: 27px; letter-spacing: .5px;
  }
  .rule { width: 130px; height: 1.5px; background: var(--blue); margin: 8px 0 10px; }
  .detail { color: var(--white); font-size: 19px; line-height: 1.35; }
  .credential {
    color: var(--red); font-weight: 600; font-size: 20px; line-height: 1.25; text-transform: uppercase;
  }

  /* Brand side */
  .edge-mark { position: absolute; display: flex; height: 92px; }
  .edge-mark .bar-blue { width: 26px; background: var(--blue); }
  .edge-mark .bar-red { width: 5px; background: var(--red); }
  .edge-mark .gap { width: 7px; }
  .edge-mark.left { left: 0; top: 128px; }
  .edge-mark.right { right: 0; top: 18px; }
  .brand { display: flex; align-items: center; gap: 12px; }
  .brand-dot { width: 34px; height: 34px; border-radius: 50%; background: var(--red); }
  .brand-name {
    color: var(--blue); font-weight: 700; font-size: 50px; letter-spacing: 1px; line-height: 1;
  }
  .brand-tagline {
    color: var(--red); font-size: 11px; letter-spacing: .5px; text-transform: uppercase; margin: 4px 0 18px 46px;
  }
  .service-area { color: var(--white); font-weight: 600; font-size: 18px; margin-bottom: 14px; }
  .call-out {
    color: var(--red); font-weight: 600; font-size: 17px; line-height: 1.25; text-transform: uppercase;
  }
</style>
</head>
<body>
  <section class="card contact">
    <div class="band top"></div>
    <h1 class="person-name">MARK DALVICK</h1>
    <div class="rule"></div>
    <p class="detail">555.014.2290</p>
    <p class="detail">dalvickhvac@example.com</p>
    <div class="rule"></div>
    <p class="credential">Licensed &amp; Insured</p>
    <p class="credential">Family Owned &amp; Operated</p>
    <div class="band bottom"></div>
  </section>

  <section class="card brand-side">
    <div class="edge-mark left"><span class="bar-blue"></span><span class="gap"></span><span class="bar-red"></span></div>
    <div class="edge-mark right"><span class="bar-red"></span><span class="gap"></span><span class="bar-blue"></span></div>
    <div class="brand">
      <span class="brand-dot"></span>
      <span class="brand-name">DALVICK'S</span>
    </div>
    <p class="brand-tagline">Air Conditioning &amp; Heating Service</p>
    <p class="service-area">Serves Ridgefield IA &amp; Surrounding Areas</p>
    <p class="call-out">Call today for all your HVAC</p>
    <p class="call-out">Refrigeration &amp; plumbing needs</p>
  </section>
</body>
</html>
```